Business Card for Multi-Brand Sportswear Company

We are looking for a business card which represents our company and the multiple brands within it.

The company: Fen Athletics (LTD)
The brands: Fen, TavaPuni, ElmStretch, Grit and Rain

Employees using these cards would be representing Fen Athletics, rather than any of the individual brands. You will see a current design within the uploaded files, to give some inspiration. The actual text of the brands is not necessary, but the logos should be on there is some format.

Our creative minds on this are stretched, so we are looking for someone to make this their own, and show us what a good business card should look like.

We may like to get these printed with spot gloss, so keep that in mind with your designs.

www.fenathletics.co.uk

Industry/Entity Type

Business

Contact Information for Business Card

Leo Pemberton-Hale
Operations Manager
(+44) 1632 960 418
Leo@fenathletics.co.uk
www.fenathletics.co.uk

Font styles to use
Sans Serif
Other font styles liked:
• Eurostile

Colors
ffffff

Requirements
Nice to have
• Dark (black) background

```html
<!DOCTYPE html>
<html lang="en">
<head>
<meta charset="utf-8">
<title>Fen Athletics – Business Card</title>
<link rel="stylesheet" href="https://fonts.googleapis.com/css2?family=Exo+2:wght@400;600;700&display=swap">
<style>
  :root {
    --backdrop: #3b3b3b;
    --card-dark: #000000;
    --card-light: #ffffff;
    --brand-red: #ec1c24;
    --ink-dark: #111111;
    --ink-light: #ffffff;
    --ink-muted: #4a4a4a;
  }
  * { box-sizing: border-box; margin: 0; padding: 0; }
  html, body {
    width: 1105px; height: 1200px; overflow: hidden;
    background: var(--backdrop);
    font-family: "Exo 2", Arial, sans-serif;
  }
  .canvas { position: relative; width: 1105px; height: 1200px; }
  .card {
    position: absolute; left: 196px; width: 720px; height: 412px;
    overflow: hidden;
  }
  .card--front { top: 146px; background: var(--card-dark); }
  .card--back  { top: 602px; background: var(--card-light); }

  .wordmark {
    position: absolute; left: 0; right: 0; text-align: center;
    font-weight: 600; letter-spacing: 1px;
  }
  .card--front .wordmark { top: 72px; font-size: 52px; color: var(--ink-light); }
  .card--back .wordmark  { top: 138px; font-size: 66px; color: var(--ink-dark); }

  .contact-band { position: absolute; left: 0; top: 0; width: 720px; height: 412px; }
  .contact {
    position: absolute; left: 60px; right: 40px; top: 220px;
    text-align: center; color: var(--ink-dark);
  }
  .contact__name { font-size: 25px; font-weight: 700; letter-spacing: 0.5px; line-height: 30px; }
  .contact__role { font-size: 19px; font-weight: 400; line-height: 28px; }
  .contact__address { font-size: 18px; margin-top: 10px; line-height: 26px; }
  .contact__row {
    display: flex; justify-content: center; gap: 16px;
    font-size: 18px; line-height: 28px;
  }
  .contact__item { display: inline-flex; align-items: center; gap: 6px; }
  .icon { width: 16px; height: 16px; fill: var(--ink-dark); }

  .brand-row {
    position: absolute; left: 0; right: 0; top: 320px;
    display: flex; justify-content: center; gap: 30px;
    font-size: 21px; font-weight: 600; color: var(--ink-muted);
  }
</style>
</head>
<body>
<main class="canvas">
  <section class="card card--front">
    <div class="wordmark">Fen Athletics</div>
    <svg class="contact-band" viewBox="0 0 720 412" aria-hidden="true">
      <path d="M70 214 L704 214 L664 376 L24 376 Z" fill="var(--brand-red)"
            stroke="var(--brand-red)" stroke-width="20" stroke-linejoin="round"/>
    </svg>
    <div class="contact">
      <p class="contact__name">OWEN THACKERAY</p>
      <p class="contact__role">Managing Director</p>
      <p class="contact__address">Marsh Lane, Elmwick, Norwich, NR9 4XT</p>
      <div class="contact__row">
        <span class="contact__item">
          <svg class="icon" viewBox="0 0 16 16"><path d="M3.5 1 L6 1 L7 4.5 L5.3 5.8 C6.2 7.8 8.2 9.8 10.2 10.7 L11.5 9 L15 10 L15 12.5 C15 13.9 13.9 15 12.5 15 C6.2 15 1 9.8 1 3.5 C1 2.1 2.1 1 3.5 1 Z"/></svg>
          +44 (0)1632 960418
        </span>
        <span class="contact__item">
          <svg class="icon" viewBox="0 0 16 16"><path d="M1 3 H15 V13 H1 Z M1.5 3.5 L8 8.5 L14.5 3.5" fill="var(--ink-dark)" stroke="var(--brand-red)" stroke-width="1.2"/></svg>
          owen@fenathletics.co.uk
        </span>
      </div>
      <div class="contact__row">
        <span class="contact__item">
          <svg class="icon" viewBox="0 0 16 16"><circle cx="8" cy="8" r="7"/><path d="M1 8 H15 M8 1 C5 4 5 12 8 15 M8 1 C11 4 11 12 8 15" fill="none" stroke="var(--brand-red)" stroke-width="1"/></svg>
          www.fenathletics.co.uk
        </span>
      </div>
    </div>
  </section>

  <section class="card card--back">
    <div class="wordmark">Fen Athletics</div>
    <div class="brand-row">
      <span class="brand">TavaPuni</span>
      <span class="brand">ElmStretch</span>
      <span class="brand">Grit and Rain</span>
      <span class="brand">Fen</span>
    </div>
  </section>
</main>
</body>
</html>
```